Our companies name is The Gilded Ladle and we specialize in craft cupcakes, what I mean by that is that we bake our cupcakes with craft beer and other alcoholic drinks. We are trying to focus on being elegant but at the same time unpretentious. Since we are incorporating beer in our cupcakes we want the business card to have our logo in the front and our information in the back.

Once we select the best design we will provide the contact information to be added. Thank you.

Industry/Entity Type

Business

Font styles to use
Decorative
Script

Requirements
Must have
• Round corners
Should not have
• Square corners

```html
<!DOCTYPE html>
<html lang="en">
<head>
<meta charset="utf-8">
<title>The Gilded Ladle – Business Card</title>
<link rel="stylesheet" href="https://fonts.googleapis.com/css2?family=Michroma&display=swap">
<style>
  :root {
    --backdrop: #5f6062;
    --card: #ffffff;
    --teal: #7ecbbd;
    --red: #e8202a;
    --ink: #1f1a1d;
    --on-teal: #ffffff;
    --radius: 16px;
  }
  * { box-sizing: border-box; margin: 0; padding: 0; }
  html, body {
    width: 1200px; height: 771px; overflow: hidden;
    background: var(--backdrop);
    font-family: "Michroma", sans-serif;
  }
  .sheet {
    width: 1200px; height: 771px;
    display: flex; align-items: center; justify-content: center; gap: 30px;
  }
  .card {
    position: relative;
    width: 560px; height: 320px;
    background: var(--card);
    border-radius: var(--radius);
    overflow: hidden;
    box-shadow: 0 10px 24px rgba(0,0,0,.35);
  }
  .card__art { position: absolute; inset: 0; }
  .brand {
    position: absolute;
    display: flex; align-items: center; gap: 10px;
    color: var(--ink);
  }
  .brand__dot {
    width: 34px; height: 34px; border-radius: 50%;
    background: var(--ink);
    flex: none;
  }
  .brand__name {
    font-size: 17px; line-height: 1.2; letter-spacing: .04em;
    text-transform: uppercase;
  }
  .card--front .brand { left: 50%; top: 50%; transform: translate(-50%, -50%); }
  .card--front .brand__name { font-size: 21px; }
  .card--front .brand__dot { width: 42px; height: 42px; }
  .card--back .brand { left: 300px; top: 62px; }

  .person {
    position: absolute; right: 300px; top: 214px;
    text-align: right; color: var(--on-teal);
    font-size: 9px; line-height: 1.7; letter-spacing: .06em;
  }
  .person__name { font-size: 12px; margin-bottom: 3px; }
  .divider {
    position: absolute; left: 273px; top: 212px;
    width: 1px; height: 88px; background: var(--on-teal);
  }
  .contacts {
    position: absolute; left: 286px; top: 214px;
    list-style: none; color: var(--on-teal);
    font-size: 9px; line-height: 1; letter-spacing: .05em;
  }
  .contacts li { display: flex; align-items: center; gap: 7px; height: 17px; }
  .contacts svg { width: 11px; height: 11px; flex: none; }
</style>
</head>
<body>
<main class="sheet">

  <section class="card card--front" aria-label="Card front">
    <div class="brand">
      <span class="brand__dot"></span>
      <span class="brand__name">The Gilded Ladle</span>
    </div>
  </section>

  <section class="card card--back" aria-label="Card back">
    <svg class="card__art" viewBox="0 0 560 320" preserveAspectRatio="none" aria-hidden="true">
      <path d="M0,118 C170,108 270,178 560,206 L560,320 L0,320 Z" fill="var(--teal)"/>
      <path d="M0,100 C170,90 270,160 560,188 L560,198 C270,170 170,100 0,110 Z" fill="var(--red)"/>
    </svg>

    <div class="brand">
      <span class="brand__dot"></span>
      <span class="brand__name">The Gilded Ladle</span>
    </div>

    <div class="person">
      <p class="person__name">Clara Mendes</p>
      <p>Owner / C.E.O</p>
      <p>Suite # 118, Elm Bldg,</p>
      <p>NY 40721</p>
    </div>

    <span class="divider"></span>

    <ul class="contacts">
      <li>
        <svg viewBox="0 0 12 12"><circle cx="6" cy="6" r="6" fill="#fff"/><path d="M4 3.2l1 1.3-.6.8a4 4 0 0 0 2.3 2.3l.8-.6 1.3 1-.6 1A5 5 0 0 1 3 4.1z" fill="var(--teal)"/></svg>
        555-210-4871
      </li>
      <li>
        <svg viewBox="0 0 12 12"><circle cx="6" cy="6" r="6" fill="#fff"/><rect x="4.2" y="2.6" width="3.6" height="6.8" rx=".8" fill="var(--teal)"/></svg>
        555-386-9024
      </li>
      <li>
        <svg viewBox="0 0 12 12"><circle cx="6" cy="6" r="6" fill="#fff"/><path d="M3 3.6h6v4.8H3z" fill="var(--teal)"/></svg>
        555-743-1596
      </li>
      <li>
        <svg viewBox="0 0 12 12"><circle cx="6" cy="6" r="6" fill="#fff"/><path d="M3 4h6v4.2H3z M3 4l3 2.3L9 4" fill="none" stroke="var(--teal)" stroke-width=".9"/></svg>
        hello@gildedladle.com
      </li>
      <li>
        <svg viewBox="0 0 12 12"><circle cx="6" cy="6" r="6" fill="#fff"/><circle cx="6" cy="6" r="3" fill="none" stroke="var(--teal)" stroke-width=".9"/><path d="M3 6h6M6 3v6" stroke="var(--teal)" stroke-width=".7"/></svg>
        www.gildedladle.com
      </li>
    </ul>
  </section>

</main>
</body>
</html>
```